Redesign of business card for Cedar Ridge Mechanical

We are looking for a new design for our business cards for Cedar Ridge Mechanical. We are a plumbing & HVAC construction company, operating on the West Coast of Canada and USA. Logo attached.
Industry/Entity Type
Construction - Plumbing & HVAC
Contact Information for Business Card
Name, address, phone numbers, email, website address
Look and feel
Each slider illustrates characteristics of the customer's brand and the style your logo design should communicate.

```html
<!DOCTYPE html>
<html lang="en">
<head>
<meta charset="utf-8">
<title>Cedar Ridge Mechanical – Business Card</title>
<link rel="stylesheet" href="https://fonts.googleapis.com/css2?family=Arimo:wght@400;700&family=Roboto+Condensed:wght@700&display=swap">
<style>
  :root {
    --canvas: #9a9a9a;
    --card-front: #ffffff;
    --card-back: #323232;
    --ink: #1c1c1c;
    --ink-soft: #7a7a7a;
    --rule: #c9c9c9;
    --paper-text: #ffffff;
  }
  * { margin: 0; padding: 0; box-sizing: border-box; }
  html, body { width: 1200px; height: 1050px; overflow: hidden; }
  body {
    background: var(--canvas);
    font-family: "Arimo", Arial, sans-serif;
    position: relative;
  }
  .card {
    position: absolute;
    left: 200px;
    width: 800px;
    height: 457px;
    border-radius: 28px;
  }
  .card--front { top: 48px; background: var(--card-front); color: var(--ink); }
  .card--back { top: 545px; background: var(--card-back); color: var(--paper-text); }

  .brand {
    position: absolute;
    left: 0; right: 0;
    display: flex;
    align-items: center;
    justify-content: center;
    gap: 16px;
    font-family: "Arimo", Arial, sans-serif;
    font-weight: 700;
    white-space: nowrap;
  }
  .brand__square { display: block; background: currentColor; }
  .card--front .brand { top: 105px; font-size: 38px; }
  .card--front .brand__square { width: 30px; height: 30px; }
  .card--back .brand { top: 160px; font-size: 52px; }
  .card--back .brand__square { width: 42px; height: 42px; }

  .holder {
    position: absolute;
    right: 440px;
    top: 262px;
    text-align: right;
  }
  .holder__name {
    font-family: "Roboto Condensed", "Arial Narrow", sans-serif;
    font-weight: 700;
    font-size: 30px;
    line-height: 1.1;
  }
  .holder__title { font-size: 21px; color: var(--ink-soft); margin-top: 2px; }

  .divider {
    position: absolute;
    left: 385px;
    top: 258px;
    width: 1px;
    height: 150px;
    background: var(--rule);
  }
  .contact {
    position: absolute;
    left: 410px;
    top: 258px;
    font-size: 21px;
    line-height: 27px;
    list-style: none;
  }
  .contact__address { margin-bottom: 4px; }
  .contact__item { display: flex; align-items: center; gap: 10px; }
  .contact__item svg { width: 16px; height: 16px; flex: none; fill: var(--ink); }

  .back__web {
    position: absolute;
    left: 0; right: 0;
    bottom: 70px;
    text-align: center;
    font-size: 24px;
    letter-spacing: 0.3px;
  }
</style>
</head>
<body>
  <section class="card card--front">
    <div class="brand"><span class="brand__square"></span>Cedar Ridge Mechanical</div>

    <div class="holder">
      <p class="holder__name">Martin Hale</p>
      <p class="holder__title">President</p>
    </div>

    <div class="divider"></div>

    <ul class="contact">
      <li class="contact__address">2471 Harbor View Road<br>Bellmont, WA 98201</li>
      <li class="contact__item">
        <svg viewBox="0 0 16 16" aria-hidden="true"><path d="M3.6 1.2l2.2 2.6-1.3 1.8c.9 2 2.4 3.6 4.4 4.5l1.8-1.3 2.6 2.2-1.2 2.6C6.6 13.4 2.6 9.4 1 3.9z"/></svg>
        (604) 5521-3087
      </li>
      <li class="contact__item">
        <svg viewBox="0 0 16 16" aria-hidden="true"><path d="M1 3h14v10H1zM2.2 4.2v.4L8 8.6l5.8-4v-.4zM2.2 6.1v5.7h11.6V6.1L8 10.1z"/></svg>
        name@cedarridgemechanical.com
      </li>
      <li class="contact__item">
        <svg viewBox="0 0 16 16" aria-hidden="true"><circle cx="8" cy="8" r="7"/></svg>
        www.cedarridgemechanical.com
      </li>
    </ul>
  </section>

  <section class="card card--back">
    <div class="brand"><span class="brand__square"></span>Cedar Ridge Mechanical</div>
    <p class="back__web">www.cedarridgemechanical.com</p>
  </section>
</body>
</html>
```